Harborline Benches business cards

I’d like a business card design that includes my logo, a tag line and my contact info. Black, textured background. My contact info color should match the orange and blue gradients. Tagline under logo: “Wooden Tables and Furniture of the Highest Quality”

Target Market(s)

High end furniture buyers

Contact Information for Business Card

Contact info, logo and tagline

```html
<!DOCTYPE html>
<html lang="en">
<head>
<meta charset="utf-8">
<title>Harborline Benches — Business Cards</title>
<link rel="stylesheet" href="https://fonts.googleapis.com/css2?family=Open+Sans:wght@700&family=Poppins:wght@400;500&display=swap">
<style>
  :root {
    --page-bg: #3c3d40;
    --card-orange: #ee7627;
    --brand-blue: #0057b0;
    --tree-white: #ffffff;
    --back-mid: #2e3139;
    --text-light: #ffffff;
    --rule-orange: #e8642a;
    --rule-gold: #e8c64a;
  }
  * { box-sizing: border-box; margin: 0; padding: 0; }
  html, body {
    width: 1093px;
    height: 1200px;
    overflow: hidden;
    background: var(--page-bg);
    font-family: "Poppins", sans-serif;
  }
  .card {
    position: absolute;
    left: 264px;
    width: 580px;
    height: 357px;
    border-radius: 24px;
    overflow: hidden;
    color: var(--text-light);
  }
  .card-front {
    top: 226px;
    background: var(--card-orange);
  }
  .front-art {
    position: absolute;
    left: 274px;
    top: 0;
    width: 306px;
    height: 100%;
    background: linear-gradient(90deg, var(--card-orange) 0%, #f6b98e 30%, var(--tree-white) 48%, #6f9fd6 62%, var(--brand-blue) 78%);
  }
  .holder-name {
    position: absolute;
    left: 35px;
    top: 48px;
    font-family: "Open Sans", sans-serif;
    font-weight: 700;
    font-size: 29px;
    line-height: 1;
    letter-spacing: -0.3px;
    white-space: nowrap;
  }
  .holder-title {
    position: absolute;
    left: 36px;
    top: 80px;
    font-size: 16.5px;
    line-height: 1;
    white-space: nowrap;
  }
  .contact-list {
    position: absolute;
    left: 36px;
    top: 159px;
    list-style: none;
  }
  .contact-list li {
    display: flex;
    align-items: center;
    gap: 7px;
    height: 21px;
    font-size: 17px;
    white-space: nowrap;
  }
  .contact-list svg {
    width: 15px;
    height: 15px;
    flex: none;
  }
  .address {
    position: absolute;
    left: 37px;
    top: 272px;
    font-size: 17px;
    line-height: 21px;
    white-space: nowrap;
  }
  .card-back {
    top: 621px;
    background: linear-gradient(160deg, #1d2025 0%, var(--back-mid) 35%, #1f2227 55%, var(--back-mid) 80%, #262930 100%);
  }
  .brand-lockup {
    position: absolute;
    left: 0;
    right: 0;
    top: 150px;
    display: flex;
    justify-content: center;
    align-items: center;
    gap: 12px;
  }
  .brand-mark {
    width: 22px;
    height: 22px;
    border-radius: 50%;
    background: var(--rule-orange);
  }
  .brand-name {
    font-weight: 500;
    font-size: 40px;
    line-height: 1;
    color: var(--rule-orange);
    white-space: nowrap;
  }
  .brand-rule {
    position: absolute;
    left: 305px;
    top: 218px;
    width: 168px;
    height: 1.5px;
    background: linear-gradient(90deg, var(--rule-orange), var(--rule-gold));
  }
  .tagline {
    position: absolute;
    left: 0;
    right: 0;
    top: 244px;
    text-align: center;
    font-size: 17px;
    letter-spacing: 0.1px;
    white-space: nowrap;
  }
</style>
</head>
<body>
  <section class="card card-front">
    <div class="front-art" role="img" aria-label="Illustration of a tree with white branches over orange and blue halves"></div>
    <h1 class="holder-name">Daniel Carver</h1>
    <p class="holder-title">Managing Director</p>
    <ul class="contact-list">
      <li>
        <svg viewBox="0 0 16 16" aria-hidden="true"><path fill="#fff" d="M3.2 1.5l2.3 2.6-1.2 1.6c.9 2 2.2 3.4 4.1 4.4l1.6-1.2 2.6 2.3-1.4 2.3C7 13.3 2.6 8.9 1 4.2z"/><path d="M9.5 2.5a4 4 0 0 1 4 4M9.5 .8a5.7 5.7 0 0 1 5.7 5.7" stroke="#fff" stroke-width="1.2" fill="none"/></svg>
        044-718 302 645
      </li>
      <li>
        <svg viewBox="0 0 16 16" aria-hidden="true"><rect x="1" y="3.5" width="14" height="9.5" fill="#fff"/><path d="M1 3.5l7 5 7-5" stroke="#ee7627" stroke-width="1.2" fill="none"/></svg>
        hello@harborline.com
      </li>
      <li>
        <svg viewBox="0 0 16 16" aria-hidden="true"><g stroke="#fff" stroke-width="1.1" fill="none"><circle cx="8" cy="8" r="6.5"/><ellipse cx="8" cy="8" rx="2.8" ry="6.5"/><path d="M1.5 8h13M2.6 4.6h10.8M2.6 11.4h10.8"/></g></svg>
        www.harborline.com
      </li>
    </ul>
    <p class="address">87, Saltmeadow Lane, Unit 4<br>30917, Eastbay Coast</p>
  </section>

  <section class="card card-back">
    <div class="brand-lockup">
      <span class="brand-mark"></span>
      <span class="brand-name">Harborline Benches</span>
    </div>
    <div class="brand-rule"></div>
    <p class="tagline">Wooden Tables and Furniture of the Highest Quality</p>
  </section>
</body>
</html>
```